Tall fern bicycle rental

would like to have a bicycle rental website that has the ability to have a calender and be able to sign a liability waiver and pay all on line, We rent fat tire vorn bicycles

```html
<!DOCTYPE html>
<html lang="en">
<head>
<meta charset="utf-8">
<title>Tall Fern Bicycle Rental</title>
<link href="https://fonts.googleapis.com/css2?family=Mulish:wght@400;600;700&family=Open+Sans:wght@400;600;700&display=swap" rel="stylesheet">
<style>
:root{
  --blue:#1a5ea8;
  --blue-bright:#2a8fd8;
  --navy:#0e2745;
  --ink:#333;
  --muted:#777;
  --cell:#ececec;
  --cell-light:#f5f5f5;
  --panel:#e4e4e4;
  --sand:#f3efe6;
}
*{box-sizing:border-box;margin:0;padding:0}
html,body{width:1200px;height:3686px;overflow:hidden;background:#fff}
body{position:relative;font-family:"Open Sans",sans-serif;color:var(--ink)}
.abs{position:absolute}
.title{font-family:"Mulish",sans-serif;font-weight:600;color:var(--blue);text-align:center;width:1200px;left:0}

/* header */
.logo{left:143px;top:52px;display:flex;align-items:center;gap:10px;font-family:"Open Sans",sans-serif;font-weight:700;color:var(--blue);font-size:17px;line-height:1.15;width:180px}
.logo-dot{width:44px;height:44px;border-radius:50%;background:var(--blue);flex:none}
.search{left:815px;top:35px;width:240px;height:40px;border:1px solid #ccc;font-size:12px;color:#999;padding:11px 14px}
.search svg{position:absolute;right:12px;top:12px}
.nav{top:106px;left:440px;width:615px;display:flex;justify-content:space-between;font-size:16px;color:#666;text-transform:uppercase}
.nav .active{color:var(--blue)}

/* hero */
.hero{left:0;top:152px;width:1200px;height:560px;background:linear-gradient(180deg,#dfe8f1 0%,#c9d9e8 40%,#7fa8c6 46%,#d9cbb4 52%,#e7dccb 100%)}
.hero-head{right:145px;top:270px;text-align:right;font-size:33px;line-height:40px;color:#1d1d1d;font-family:"Open Sans",sans-serif}
.btn-solid{background:var(--blue);color:#fff;text-transform:uppercase;font-size:15px;text-align:center;font-weight:600}
.arrow{width:44px;height:44px;border-radius:50%;background:var(--blue-bright);display:flex;align-items:center;justify-content:center}

/* welcome */
.welcome-p{left:143px;top:842px;width:912px;font-size:13px;line-height:27px;color:#555;text-align:center}
.btn-line{border:1.5px solid #999;border-radius:3px;color:#555;font-size:14px;text-align:center;text-transform:uppercase}

/* bicycles */
.band{left:0;width:1200px;background:linear-gradient(180deg,#e4ecef 0%,#cfe1e8 35%,#9ccad7 55%,#e9e6df 80%,var(--sand) 100%)}
.bike{width:250px;height:165px;top:1210px;background:linear-gradient(180deg,#fff0,#cfd8dc 60%,#fff0);border-radius:8px}
.bike-name{width:250px;text-align:center;font-family:"Mulish",sans-serif;font-size:19px;color:var(--blue);top:1384px}
.bike-btn{width:112px;height:40px;top:1418px;border:1.5px solid var(--blue);background:#fff8;color:var(--blue);font-size:16px;line-height:37px;text-align:center}

/* calendar */
.cal{left:143px;top:1741px;width:433px;display:grid;grid-template-columns:repeat(7,1fr);gap:2px}
.cal .hd{background:var(--blue);color:#fff;font-size:15px;height:48px;line-height:48px;text-align:center;margin-bottom:-2px}
.cal .d{background:var(--cell);height:60px;line-height:60px;text-align:center;font-family:"Mulish",sans-serif;font-size:19px;color:#333}
.cal .d.off{color:#999}
.cal .d.mark{color:var(--blue);background:var(--cell-light)}
.event{left:624px;width:432px;height:111px;background:var(--panel);display:flex;align-items:center}
.event .date{width:107px;text-align:center;font-family:"Mulish",sans-serif;color:var(--blue);border-right:1px solid #bbb;height:75px;line-height:1}
.event .date span{display:block;font-size:16px;margin-bottom:2px}
.event .date b{font-weight:400;font-size:46px}
.event p{padding:0 18px 0 21px;font-size:12.5px;line-height:21px;color:#444}
.viewall{left:624px;top:2103px;width:432px;height:59px;background:var(--panel);text-align:center;line-height:59px;color:var(--blue);font-size:16px;text-decoration:underline}

/* gallery */
.photo{position:absolute}
.promo{top:3155px;width:449px;height:255px}
.promo-head{font-family:"Mulish",sans-serif;font-weight:700;color:#fff;font-size:23px;line-height:28px;text-align:right;text-transform:uppercase}

/* footer */
.footer{left:0;top:3450px;width:1200px;height:236px;background:var(--navy)}
.foot-links{left:143px;top:3588px;font-size:11.5px;color:#7ea8cf}
.foot-links span{margin:0 8px}
.copy{left:143px;top:3622px;font-size:11.5px;color:#7ea8cf}
.social{width:16px;height:16px;border-radius:50%;background:#4d7aa6;top:3604px}
</style>
</head>
<body>

<!-- header -->
<div class="abs logo"><div class="logo-dot"></div><div>Tall Fern<br>Bicycle Rental</div></div>
<div class="abs search">Search
  <svg width="16" height="16" viewBox="0 0 16 16"><circle cx="6.5" cy="6.5" r="4.5" fill="none" stroke="#1a5ea8" stroke-width="2.2"/><line x1="10" y1="10" x2="14" y2="14" stroke="#1a5ea8" stroke-width="2.5"/></svg>
</div>
<nav class="abs nav"><span class="active">Our Bicycles</span><span>Gallery</span><span>Reviews</span><span>About Us</span><span>Contact Us</span></nav>

<!-- hero -->
<div class="abs hero" role="img" aria-label="Two cyclists with bicycles on a sandy beach by the sea"></div>
<svg class="abs" style="left:0;top:152px" width="1200" height="560" viewBox="0 0 1200 560">
  <path d="M0 460 Q600 640 1200 460 L1200 560 L0 560Z" fill="#fff"/>
  <path d="M0 460 Q600 640 1200 460 L1200 470 Q600 662 0 470Z" fill="#2a8fd8"/>
</svg>
<div class="abs hero-head">Pellentesque convallis molestie<br>enim sit amet efficitur</div>
<div class="abs btn-solid" style="left:927px;top:362px;width:128px;height:48px;line-height:48px">Book Now</div>
<div class="abs arrow" style="left:51px;top:361px"><svg width="14" height="18" viewBox="0 0 14 18"><path d="M10 2 L3 9 L10 16" fill="none" stroke="#fff" stroke-width="3"/></svg></div>
<div class="abs arrow" style="left:1103px;top:361px"><svg width="14" height="18" viewBox="0 0 14 18"><path d="M4 2 L11 9 L4 16" fill="none" stroke="#fff" stroke-width="3"/></svg></div>

<!-- welcome -->
<h1 class="abs title" style="top:780px;font-size:34px">Welcome to Tall Fern Bicycle Rental</h1>
<p class="abs welcome-p">Fusce sollicitudin lorem et luctus volutpat. Proin placerat dapibus gravida. In tristique tristique nulla eget hendrerit. Maecenas vel tortor accumsan quam varius imperdiet vel eget elit. Aenean facilisis tincidunt lectus, id dictum nisi luctus eget. Vivamus efficitur ex condimentum, malesuada eros eget, feugiat nibh. Sed tellus ex, imperdiet eget gravida sit amet, volutpat eget turpis.</p>
<div class="abs btn-line" style="left:540px;top:940px;width:120px;height:40px;line-height:37px">Read More</div>

<!-- bicycles -->
<div class="abs band" style="top:997px;height:610px" role="img" aria-label="Blurred beach and sea background"></div>
<svg class="abs" style="left:0;top:997px" width="1200" height="610" viewBox="0 0 1200 610">
  <path d="M0 0 Q600 150 1200 0 L1200 0 L0 0Z" fill="#fff"/>
  <path d="M0 518 Q600 690 1200 518 L1200 610 L0 610Z" fill="#fff"/>
  <path d="M0 512 Q600 680 1200 512 L1200 522 Q600 702 0 522Z" fill="#2a8fd8"/>
</svg>
<h2 class="abs title" style="top:1140px;font-size:33px">Our Bicycles</h2>
<div class="abs arrow" style="left:51px;top:1271px"><svg width="14" height="18" viewBox="0 0 14 18"><path d="M10 2 L3 9 L10 16" fill="none" stroke="#fff" stroke-width="3"/></svg></div>
<div class="abs arrow" style="left:1103px;top:1271px"><svg width="14" height="18" viewBox="0 0 14 18"><path d="M4 2 L11 9 L4 16" fill="none" stroke="#fff" stroke-width="3"/></svg></div>
<div class="abs bike" style="left:144px" role="img" aria-label="Yellow road bicycle"></div>
<div class="abs bike" style="left:474px" role="img" aria-label="Black fat tire bicycle"></div>
<div class="abs bike" style="left:803px" role="img" aria-label="Black road bicycle"></div>
<div class="abs bike-name" style="left:144px">Aliquam erat</div>
<div class="abs bike-name" style="left:474px">Pellentesque</div>
<div class="abs bike-name" style="left:803px">Cras augue</div>
<div class="abs bike-btn" style="left:213px">Book Now</div>
<div class="abs bike-btn" style="left:543px">Book Now</div>
<div class="abs bike-btn" style="left:872px">Book Now</div>

<!-- calendar -->
<h2 class="abs title" style="top:1674px;font-size:33px">Calendar</h2>
<div class="abs cal">
  <div class="hd">Mon</div><div class="hd">Tue</div><div class="hd">Wed</div><div class="hd">Thu</div><div class="hd">Fri</div><div class="hd">Sat</div><div class="hd">Sun</div>
  <div class="d off">28</div><div class="d off">29</div><div class="d off">30</div><div class="d off">31</div><div class="d">1</div><div class="d mark">2</div><div class="d">3</div>
  <div class="d">4</div><div class="d mark">5</div><div class="d">6</div><div class="d">7</div><div class="d">8</div><div class="d">9</div><div class="d">10</div>
  <div class="d">11</div><div class="d">12</div><div class="d">13</div><div class="d">14</div><div class="d">15</div><div class="d mark">16</div><div class="d">17</div>
  <div class="d">18</div><div class="d">19</div><div class="d">20</div><div class="d mark">21</div><div class="d">22</div><div class="d">23</div><div class="d">24</div>
  <div class="d">25</div><div class="d">26</div><div class="d mark">27</div><div class="d">28</div><div class="d">29</div><div class="d">30</div><div class="d">31</div>
  <div class="d off">1</div><div class="d off">2</div><div class="d off">3</div><div class="d off">4</div><div class="d off">5</div><div class="d off">6</div><div class="d off">7</div>
</div>
<div class="abs event" style="top:1741px"><div class="date"><span>May</span><b>23</b></div><p>Vestibulum condimentum, risus ut posuere cursus, velit justo accumsan sem, lobortis aliquet metus dui eu libero. Pellentesque a imperdiet</p></div>
<div class="abs event" style="top:1864px"><div class="date"><span>May</span><b>24</b></div><p>Fusce sollicitudin lorem et luctus volutpat. Proin placerat dapibus gravida. In tristique tristique nulla eget hendrerit.</p></div>
<div class="abs event" style="top:1987px"><div class="date"><span>May</span><b>28</b></div><p>Maecenas vel tortor accumsan quam varius imperdiet vel eget elit. Aenean facilisis tincidunt lectus, id dictum nisi luctus eget.</p></div>
<div class="abs viewall">VIEW ALL</div>

<!-- gallery -->
<div class="abs band" style="top:2240px;height:840px" role="img" aria-label="Blurred beach and sea background"></div>
<svg class="abs" style="left:0;top:2240px" width="1200" height="840" viewBox="0 0 1200 840">
  <path d="M0 0 Q600 150 1200 0Z" fill="#fff"/>
  <path d="M0 748 Q600 920 1200 748 L1200 840 L0 840Z" fill="#fff"/>
  <path d="M0 742 Q600 910 1200 742 L1200 752 Q600 932 0 752Z" fill="#2a8fd8"/>
</svg>
<h2 class="abs title" style="top:2385px;font-size:33px">Gallery</h2>
<div class="photo" style="left:143px;top:2451px;width:453px;height:271px;background:linear-gradient(180deg,#6f7a86,#e8b070 45%,#c56a2a 60%,#3a2418)" role="img" aria-label="Two cyclists on a boardwalk at sunset"></div>
<div class="photo" style="left:603px;top:2451px;width:223px;height:160px;background:linear-gradient(180deg,#bcd6e6,#4f86a6 50%,#8a6b4e)" role="img" aria-label="Bicycle on rocks by the sea"></div>
<div class="photo" style="left:832px;top:2451px;width:224px;height:160px;background:linear-gradient(180deg,#d8eef5,#3aa7c4 55%,#b5a89a)" role="img" aria-label="Person with bicycle cheering by the sea"></div>
<div class="photo" style="left:143px;top:2728px;width:224px;height:160px;background:linear-gradient(180deg,#c9e4f2,#eaf2f5 50%,#9bb0bc)" role="img" aria-label="Couple riding bicycles by the beach"></div>
<div class="photo" style="left:372px;top:2728px;width:224px;height:160px;background:linear-gradient(180deg,#4c9ac8,#2a7fb0 55%,#6a8ea0)" role="img" aria-label="Cyclist riding along the sea"></div>
<div class="photo" style="left:603px;top:2618px;width:453px;height:270px;background:linear-gradient(180deg,#5e86c4,#a9c2e3 45%,#3e7fb0 58%,#c9aa86)" role="img" aria-label="Two bicycles with baskets on a beach"></div>
<div class="abs btn-solid" style="left:536px;top:2913px;width:128px;height:47px;line-height:47px">View All</div>

<!-- promos -->
<div class="abs promo" style="left:143px;background:linear-gradient(90deg,#6e5a48,#a98c6e 35%,#d9c4a2 70%,#4f98b8)" role="img" aria-label="Red bicycle by a wooden beach fence"></div>
<div class="abs promo-head" style="left:143px;top:3243px;width:432px">Aenean Facilisis<br>Tincidunt Lectus</div>
<div class="abs btn-solid" style="left:448px;top:3301px;width:127px;height:45px;line-height:45px">Book Now</div>
<div class="abs promo" style="left:607px;background:linear-gradient(180deg,#b4c7d6,#8ea6b8 40%,#d6d2cb 70%,#c7c0b4)" role="img" aria-label="Fat tire bicycle on a sandy beach"></div>
<div class="abs promo-head" style="left:607px;top:3262px;width:432px">Etiam Mattis Augue</div>
<div class="abs btn-solid" style="left:912px;top:3301px;width:127px;height:45px;line-height:45px">Read More</div>

<!-- footer -->
<div class="abs footer"></div>
<svg class="abs" style="left:0;top:3440px" width="1200" height="90" viewBox="0 0 1200 90">
  <path d="M0 0 L1200 0 L1200 10 Q600 120 0 10Z" fill="#fff"/>
  <path d="M0 10 Q600 120 1200 10 L1200 20 Q600 140 0 20Z" fill="#2a8fd8"/>
</svg>
<div class="abs foot-links">Our Bicycles<span>|</span>Gallery<span>|</span>Reviews<span>|</span>About Us<span>|</span>Contact Us</div>
<div class="abs copy">Copyright &copy; 2020 &nbsp;Tall Fern Bicycle Rental. &nbsp;&nbsp;All rights reserved.</div>
<div class="abs social" style="left:991px"></div>
<div class="abs social" style="left:1035px"></div>

</body>
</html>
```